New LLC consulting company needs a business card design

I need a business card design for new company in Alexandria Virginia called TK Verdane Consulting LLC. The company is focused on consulting for defense and national security issues with expertise in nuclear and space topics. I would like to see designs that are simple and I am open to colors except for brown.

Target Market(s)

All businesses that are seeking consulting help

Industry/Entity Type

Consulting

Contact Information for Business Card

Name of company - TK Verdane Consulting LLC; name (Delia Pratt) President; email: prattdq47@mailvessa.com; Phone: 703-555-0142

Requirements
Must have
• The details described above
Nice to have
• I'm open to all ideas
Should not have
• No brown

```html
<!DOCTYPE html>
<html lang="en">
<head>
<meta charset="UTF-8">
<title>Delia Pratt — Business Card</title>
<link href="https://fonts.googleapis.com/css2?family=Montserrat:wght@400;700&display=swap" rel="stylesheet">
<style>
  :root {
    --backdrop: #999999;
    --card: #ffffff;
    --ink: #000000;
    --ink-soft: #2b2b2b;
    --rule: #111111;
  }
  * { margin: 0; padding: 0; box-sizing: border-box; }
  html, body {
    width: 1200px;
    height: 1059px;
    overflow: hidden;
    background: var(--backdrop);
    font-family: "Montserrat", sans-serif;
  }
  .canvas {
    position: relative;
    width: 1200px;
    height: 1059px;
  }
  .business-card {
    position: absolute;
    left: 234px;
    top: 320px;
    width: 732px;
    height: 419px;
    background: var(--card);
    border-radius: 26px;
  }
  .company-name {
    position: absolute;
    left: 0;
    right: 0;
    top: 70px;
    text-align: center;
    font-weight: 700;
    font-size: 20px;
    line-height: 26px;
    color: var(--ink);
    letter-spacing: 2px;
    text-transform: uppercase;
  }
  .person-name {
    position: absolute;
    left: 0;
    right: 0;
    top: 136px;
    text-align: center;
    font-weight: 700;
    font-size: 36px;
    line-height: 44px;
    color: var(--ink);
    letter-spacing: 0.2px;
  }
  .person-title {
    position: absolute;
    left: 0;
    right: 0;
    top: 184px;
    text-align: center;
    font-weight: 400;
    font-size: 20px;
    line-height: 26px;
    color: var(--ink-soft);
    letter-spacing: 0.6px;
  }
  .divider {
    position: absolute;
    left: 39px;
    width: 655px;
    top: 228px;
    height: 1.5px;
    background: var(--rule);
  }
  .contact {
    position: absolute;
    top: 250px;
    display: flex;
    align-items: center;
    gap: 8px;
    font-size: 19px;
    line-height: 26px;
    color: var(--ink-soft);
    letter-spacing: 0.4px;
    white-space: nowrap;
  }
  .contact--email { left: 40px; }
  .contact--phone { right: 38px; }
  .contact-icon { flex: none; fill: var(--ink); }
</style>
</head>
<body>
<main class="canvas">
  <section class="business-card">
    <p class="company-name">TK Verdane Consulting LLC</p>
    <h1 class="person-name">Delia Pratt</h1>
    <p class="person-title">President</p>
    <div class="divider"></div>
    <div class="contact contact--email">
      <svg class="contact-icon" width="15" height="11" viewBox="0 0 15 11" aria-hidden="true">
        <rect x="0" y="0" width="15" height="11" fill="var(--ink)"/>
        <path d="M0.6 0.9L7.5 6.2 14.4 0.9" stroke="#fff" stroke-width="1.1" fill="none"/>
      </svg>
      <span>prattdq47@mailvessa.com</span>
    </div>
    <div class="contact contact--phone">
      <svg class="contact-icon" width="18" height="18" viewBox="0 0 24 24" aria-hidden="true">
        <path d="M6.6 10.8a15.2 15.2 0 0 0 6.6 6.6l2.2-2.2a1 1 0 0 1 1-.25 11.4 11.4 0 0 0 3.6.57 1 1 0 0 1 1 1V20a1 1 0 0 1-1 1A17 17 0 0 1 3 4a1 1 0 0 1 1-1h3.5a1 1 0 0 1 1 1c0 1.25.2 2.45.57 3.57a1 1 0 0 1-.25 1z"/>
        <path d="M14 3.2a7 7 0 0 1 6.8 6.8 M13.8 6.4a3.8 3.8 0 0 1 3.8 3.8" stroke="var(--ink)" stroke-width="2" fill="none" stroke-linecap="round"/>
      </svg>
      <span>703-555-0142</span>
    </div>
  </section>
</main>
</body>
</html>
```